Explosive, chemical reaction of creativity!

Web design for a digital marketing company. The unconventional is encouraged!
This is for a cool, young, geographically diverse company (sketchhive... you are all part of our team!!!)... we build websites but our real specialty is "search experience optimization".... creating conversion focused content, SEO (including content), and social media.

Target Market(s)

small to medium size businesses, law firms, medical practices, municipalities

Industry/Entity Type

Marketing

Number of Pages Required

2 page

Requirements
Must have
• WOW
• something different and special... we've been playing with a science theme (www.fernquillmedia.marketing) but we are open to different looks, layouts, etc.
• we nee a homepage design and an interior page design
• content needs to include: Marketing Catalysts (about us), Our Formula (services), Chemical Reactions(Results/Our Clients),
• FREE Online Prism Check
• Let us put together an objective snapshot of your digital presence for you.
Nice to have
• we are open to the use of background video (chemical reaction???)
• we are open to cool and different imagery
Should not have
• template look like most other websites

```html
<!DOCTYPE html>
<html lang="en">
<head>
<meta charset="utf-8">
<title>Fernquill Media — Home</title>
<link href="https://fonts.googleapis.com/css2?family=Raleway:wght@400;500;600&family=Open+Sans:wght@400;600&display=swap" rel="stylesheet">
<style>
:root{
  --cobalt:#0a4fa0;
  --cobalt-dark:#073b7a;
  --sky:#1ba8f0;
  --sky-light:#5cc4f6;
  --charcoal:#333333;
  --ink:#2b2b2b;
  --muted:#8a8a8a;
  --band:#e3e3e3;
  --footer:#0b0b0b;
  --footer-bar:#1a1a1a;
  --footer-text:#d0d0d0;
  --white:#ffffff;
}
*{box-sizing:border-box;margin:0;padding:0}
html,body{width:1200px;height:2913px;overflow:hidden}
body{position:relative;background:var(--white);font-family:"Open Sans",Arial,sans-serif;color:var(--ink)}
.abs{position:absolute}
h1,h2,h3{font-family:"Raleway",Arial,sans-serif;font-weight:400}

/* header */
.site-header{left:0;top:0;width:1200px;height:100px;background:var(--white)}
.brand{left:172px;top:30px;display:flex;align-items:center;gap:12px}
.brand-mark{width:32px;height:32px;background:var(--cobalt)}
.brand-name{font-family:"Raleway",sans-serif;font-weight:600;font-size:24px;color:var(--cobalt-dark);letter-spacing:1px}
.main-nav{left:0;top:38px;width:1200px;font-size:13px;font-family:"Raleway",sans-serif;font-weight:500}
.main-nav a{position:absolute;color:#222;text-decoration:none;white-space:nowrap}
.main-nav a.active{color:var(--cobalt)}
.nav-underline{left:505px;top:74px;width:44px;height:2px;background:#222}

/* hero */
.hero{left:0;top:100px;width:1200px;height:520px;background:linear-gradient(135deg,#163f86 0%,#1f5bb4 45%,#14458f 100%)}
.hero-title{left:0;top:230px;width:1200px;text-align:center;color:var(--white);font-size:37px;line-height:49px}
.hero-sub{left:0;top:345px;width:1200px;text-align:center;color:#e6eefa;font-size:15px;line-height:26px}
.about-bg{left:0;top:540px;width:1200px;height:348px}
.slider-dots{left:556px;top:579px;display:flex;gap:4px}
.slider-dots span{width:16px;height:16px;border-radius:50%;background:var(--white)}
.slider-dots span.off{background:transparent;border:2px solid var(--white)}
.about-title{left:0;top:670px;width:1200px;text-align:center;color:var(--white);font-size:27px}
.about-text{left:240px;top:714px;width:720px;text-align:center;color:#d8d8d8;font-size:11.5px;line-height:26px}
.press-row{left:224px;top:808px;width:760px;display:flex;justify-content:space-between;align-items:center}
.press-badge{height:30px;background:#5c5c5c;border-radius:3px}

/* formula */
.formula-title{left:0;top:945px;width:1200px;text-align:center;font-size:28px;color:#333}
.formula-sub{left:0;top:992px;width:1200px;text-align:center;font-size:17px;color:#555;font-family:"Raleway",sans-serif}
.service{width:220px;text-align:center}
.service-icon{margin:0 auto;width:106px;height:106px;border-radius:50%;border:2px solid var(--cobalt);padding:4px}
.service-icon div{width:94px;height:94px;border-radius:50%;background:var(--cobalt);display:flex;align-items:center;justify-content:center}
.service-name{margin-top:18px;font-family:"Raleway",sans-serif;font-size:16px;color:var(--cobalt);letter-spacing:.5px}
.service-text{margin-top:6px;font-size:11px;line-height:19px;color:#777}

/* stats */
.stats-band{left:0;top:1359px;width:1200px;height:175px;background:var(--band)}
.stat{width:170px;text-align:center}
.stat-hex{display:block;margin:0 auto}
.stat-value{margin-top:22px;font-family:"Raleway",sans-serif;font-size:25px;color:#222}
.stat-text{margin-top:6px;font-size:11px;line-height:17px;color:#777}

/* snapshot */
.snapshot{left:0;top:1540px;width:1200px;height:380px;background:var(--sky)}
.rocket-art{left:205px;top:1600px;width:320px;height:270px;border-radius:12px;background:linear-gradient(180deg,var(--sky-light) 0%,#3bb6f3 100%)}
.snapshot-title{left:593px;top:1612px;color:var(--white);font-size:25px}
.snapshot-sub{left:593px;top:1652px;color:var(--white);font-size:17px;font-family:"Raleway",sans-serif}
.snapshot-text{left:593px;top:1696px;width:360px;color:#bfe6fb;font-size:10.5px;line-height:18px}
.btn-outline{display:inline-block;border:1.5px solid var(--white);color:var(--white);font-size:13px;text-align:center;text-decoration:none}
.snapshot-btn{left:594px;top:1771px;width:117px;height:36px;line-height:33px}

/* blogs */
.blogs-title{left:192px;top:2044px;font-size:28px;color:#333}
.blog-arrows{left:957px;top:2048px;display:flex;gap:8px}
.blog-arrows span{width:24px;height:24px;border-radius:50%;background:#dcdcdc;display:flex;align-items:center;justify-content:center}
.blog{width:380px}
.blog-title{font-family:"Raleway",sans-serif;font-size:16px;color:#222;font-weight:500}
.blog-text{margin-top:12px;font-size:11px;line-height:21px;color:#8a8a8a}
.blog-date{margin-top:10px;font-size:11.5px;color:#333}
.btn-solid{display:block;margin-top:12px;width:99px;height:34px;line-height:34px;background:var(--cobalt);color:var(--white);font-size:12px;text-align:center;text-decoration:none}

/* prism check */
.prism{left:0;top:2344px;width:1200px;height:252px;background:linear-gradient(180deg,#0a1d4a 0%,#0d3c8e 45%,#0a2f74 100%)}
.prism-title{left:0;top:2408px;width:1200px;text-align:center;color:var(--white);font-size:26px}
.prism-sub{left:0;top:2450px;width:1200px;text-align:center;color:#e8eefb;font-size:16px;font-family:"Raleway",sans-serif}
.prism-btn{left:542px;top:2486px;width:122px;height:39px;line-height:36px}

/* footer */
.site-footer{left:0;top:2596px;width:1200px;height:259px;background:var(--footer)}
.footer-col{top:2652px;color:var(--footer-text)}
.footer-col h3{font-size:18px;color:var(--white);margin-bottom:16px}
.footer-col li{list-style:none;font-size:12.5px;line-height:25px;color:var(--footer-text)}
.social li{display:flex;align-items:center;gap:12px}
.social i{display:inline-block;width:11px;height:11px;background:var(--white)}
.footer-bar{left:0;top:2855px;width:1200px;height:58px;background:var(--footer-bar)}
.copyright{left:183px;top:2873px;font-size:10.5px;color:#aaa}
</style>
</head>
<body>

<header class="site-header abs">
  <div class="brand abs"><span class="brand-mark"></span><span class="brand-name">Fernquill Media</span></div>
  <nav class="main-nav abs">
    <a class="active" style="left:509px">Home</a>
    <a style="left:565px">Marketing Catalysts</a>
    <a style="left:707px">Our Formula</a>
    <a style="left:806px">Chemical Reactions</a>
    <a style="left:948px">Contact us</a>
  </nav>
  <div class="nav-underline abs"></div>
</header>

<section class="hero abs" role="img" aria-label="Photo of a team working around a table with laptops, notebooks and coffee cups, tinted cobalt blue"></section>
<svg class="about-bg abs" viewBox="0 540 1200 348" width="1200" height="348" aria-hidden="true">
  <path d="M0 553 Q600 670 1200 553 L1200 888 L0 888 Z" fill="#333333"/>
</svg>
<h1 class="hero-title abs">It's not rocket science,<br>it's Fernquill science!</h1>
<p class="hero-sub abs">Sales is the chemical reaction that results from "our formula" which is the<br>right combination of our digital marketing services.</p>
<div class="slider-dots abs"><span class="off"></span><span></span><span></span><span></span></div>

<h2 class="about-title abs">About Our Company</h2>
<p class="about-text abs">Quisque dignissim congue leo Mauris vel lacus vitae felis vestibulum volutpat Etiam est nunc venenatis in tristique eu im-<br>perdiet ac nisl Cum sociis natoque penatibus et magnis dis parturient montes nascetur ridiculus</p>
<div class="press-row abs">
  <span class="press-badge" style="width:58px"></span>
  <span class="press-badge" style="width:92px"></span>
  <span class="press-badge" style="width:88px"></span>
  <span class="press-badge" style="width:96px"></span>
  <span class="press-badge" style="width:76px"></span>
  <span class="press-badge" style="width:170px"></span>
</div>

<h2 class="formula-title abs">The Perfect Digital Marketing Formula!</h2>
<p class="formula-sub abs">Get the right message in front of the right people.</p>

<div class="service abs" style="left:229px;top:1036px">
  <div class="service-icon"><div>
    <svg width="46" height="42" viewBox="0 0 46 42" fill="none" stroke="#fff" stroke-width="3"><rect x="2" y="2" width="42" height="38" rx="2"/><line x1="2" y1="11" x2="44" y2="11"/><rect x="9" y="17" width="12" height="10" fill="#fff"/><line x1="25" y1="18" x2="37" y2="18"/><line x1="25" y1="25" x2="37" y2="25"/><line x1="9" y1="33" x2="37" y2="33"/></svg>
  </div></div>
  <div class="service-name">WEBSITE</div>
  <p class="service-text">ontes nascetur ridiculus mus In iaculis facilisis massa Etiam eu urna Sed porta Suspendisse quam</p>
</div>
<div class="service abs" style="left:499px;top:1036px">
  <div class="service-icon"><div>
    <svg width="46" height="40" viewBox="0 0 46 40" fill="none" stroke="#fff" stroke-width="3"><rect x="8" y="2" width="36" height="36" rx="2"/><path d="M8 10 H2 V34 a4 4 0 0 0 8 0"/><rect x="14" y="9" width="12" height="10" fill="#fff"/><line x1="30" y1="10" x2="38" y2="10"/><line x1="30" y1="17" x2="38" y2="17"/><line x1="14" y1="26" x2="38" y2="26"/><line x1="14" y1="32" x2="38" y2="32"/></svg>
  </div></div>
  <div class="service-name">CONTENT</div>
  <p class="service-text">ontes nascetur ridiculus mus In iaculis facilisis massa Etiam eu urna Sed porta Suspendisse quam</p>
</div>
<div class="service abs" style="left:766px;top:1036px">
  <div class="service-icon"><div>
    <svg width="44" height="44" viewBox="0 0 44 44" fill="#fff" stroke="#fff" stroke-width="3"><circle cx="33" cy="9" r="6"/><circle cx="10" cy="22" r="6"/><circle cx="33" cy="35" r="6"/><line x1="10" y1="22" x2="33" y2="9"/><line x1="10" y1="22" x2="33" y2="35"/></svg>
  </div></div>
  <div class="service-name">SOCIAL</div>
  <p class="service-text">ontes nascetur ridiculus mus In iaculis facilisis massa Etiam eu urna Sed porta Suspendisse quam</p>
</div>

<div class="stats-band abs"></div>
<div class="stat abs" style="left:200px;top:1300px">
  <svg class="stat-hex" width="100" height="110" viewBox="0 0 100 110"><polygon points="50,3 96,29 96,81 50,107 4,81 4,29" fill="#fff" stroke="#d4d4d4" stroke-width="2"/><g fill="#c8c8c8"><rect x="30" y="40" width="32" height="24" rx="4"/><path d="M62 45 h6 a6 6 0 0 1 0 12 h-6 v-4 h5 a2 2 0 0 0 0-4 h-5z"/><rect x="25" y="68" width="48" height="4" rx="2"/></g></svg>
  <div class="stat-value">93%</div>
  <p class="stat-text">Online experiences begin with a search engine</p>
</div>
<div class="stat abs" style="left:408px;top:1300px">
  <svg class="stat-hex" width="100" height="110" viewBox="0 0 100 110"><polygon points="50,3 96,29 96,81 50,107 4,81 4,29" fill="#fff" stroke="#d4d4d4" stroke-width="2"/><rect x="35" y="33" width="30" height="44" rx="4" fill="none" stroke="#c8c8c8" stroke-width="4"/><circle cx="50" cy="71" r="2" fill="#c8c8c8"/></svg>
  <div class="stat-value">70%</div>
  <p class="stat-text">Of the links search users click on are organic</p>
</div>
<div class="stat abs" style="left:616px;top:1300px">
  <svg class="stat-hex" width="100" height="110" viewBox="0 0 100 110"><polygon points="50,3 96,29 96,81 50,107 4,81 4,29" fill="#fff" stroke="#d4d4d4" stroke-width="2"/><g fill="#c8c8c8"><polygon points="50,28 62,46 38,46"/><polygon points="50,38 66,58 34,58"/><polygon points="50,48 70,70 30,70"/><rect x="46" y="70" width="8" height="10"/></g></svg>
  <div class="stat-value">70%</div>
  <p class="stat-text">Of US population has at least one social networking profile</p>
</div>
<div class="stat abs" style="left:822px;top:1300px">
  <svg class="stat-hex" width="100" height="110" viewBox="0 0 100 110"><polygon points="50,3 96,29 96,81 50,107 4,81 4,29" fill="#fff" stroke="#d4d4d4" stroke-width="2"/><g fill="#c8c8c8"><polygon points="50,28 62,46 38,46"/><polygon points="50,38 66,58 34,58"/><polygon points="50,48 70,70 30,70"/><rect x="46" y="70" width="8" height="10"/></g></svg>
  <div class="stat-value">50%</div>
  <p class="stat-text">Of companies are using digital marketing but don't have a plan</p>
</div>

<section class="snapshot abs" role="img" aria-label="Sky blue band whose lower edge is a row of white cartoon clouds"></section>
<div class="rocket-art abs" role="img" aria-label="Illustration of a rocket launching among marketing icons: gear, magnifier, chat bubble, chart and light bulb"></div>
<h2 class="snapshot-title abs">Let us put together an objective</h2>
<p class="snapshot-sub abs">snapshot of your digital presence for you.</p>
<p class="snapshot-text abs">Duis quam Nam eget lacus Aliquam erat volutpat Quisque digni-ssim congue leo Mauris vel lacus vitae felis vestibulum volutpat Etiam est nunc venenatis in tristique eu imperdiet a</p>
<a class="btn-outline snapshot-btn abs">Read More</a>

<h2 class="blogs-title abs">Latest Blogs</h2>
<div class="blog-arrows abs">
  <span><svg width="8" height="10" viewBox="0 0 8 10"><path d="M6 1 L2 5 L6 9" fill="none" stroke="#666" stroke-width="1.6"/></svg></span>
  <span><svg width="8" height="10" viewBox="0 0 8 10"><path d="M2 1 L6 5 L2 9" fill="none" stroke="#666" stroke-width="1.6"/></svg></span>
</div>
<article class="blog abs" style="left:192px;top:2108px">
  <h3 class="blog-title">A Little Bird Told Me – 5 Reasons for Tweeting</h3>
  <p class="blog-text">volutpat Etiam est nunc venenatis in tristique eu imperdiet ac nisl Cum sociis natoque penatibus et magnis dis parturient montes na-scetur ridiculus mus In iaculis facilisis massa</p>
  <p class="blog-date">05/14/2016</p>
  <a class="btn-solid">Read More</a>
</article>
<article class="blog abs" style="left:645px;top:2108px">
  <h3 class="blog-title">The Revolution Will Now Be Optimized</h3>
  <p class="blog-text">volutpat Etiam est nunc venenatis in tristique eu imperdiet ac nisl Cum sociis natoque penatibus et magnis dis parturient montes na-scetur ridiculus mus In iaculis facilisis massa</p>
  <p class="blog-date">05/14/2016</p>
  <a class="btn-solid">Read More</a>
</article>

<section class="prism abs" role="img" aria-label="Background image of glowing digital technology icons and hexagons in deep blue"></section>
<h2 class="prism-title abs">FREE Online Prism Check</h2>
<p class="prism-sub abs">Proin dui lectus cursus eu mattis laoreet viverra sit amet quam Curabitur</p>
<a class="btn-outline prism-btn abs">Get Started</a>

<footer class="site-footer abs"></footer>
<div class="footer-col abs" style="left:192px"><h3>Company</h3><ul><li>Home</li><li>Marketing Catalysts</li><li>Our Formula</li><li>Chemical Reactions</li></ul></div>
<div class="footer-col abs" style="left:373px"><h3>Services</h3><ul><li>Nullam enim</li><li>Leo egestas</li><li>Condimentum</li><li>At laoreet</li></ul></div>
<div class="footer-col abs" style="left:538px"><h3>Resources</h3><ul><li>FAQ</li><li>Career</li><li>Contact</li></ul></div>
<div class="footer-col abs" style="left:693px"><h3>Support</h3><ul><li>Term of Use</li><li>Contact us</li></ul></div>
<div class="footer-col social abs" style="left:880px;top:2648px"><h3>Social</h3><ul><li><i></i>Circlepage</li><li><i></i>Chirpline</li><li><i></i>Searchplus</li><li><i></i>Clipstream</li></ul></div>
<div class="footer-bar abs"></div>
<p class="copyright abs">© 2016 Company Name&nbsp; All right reserved</p>

</body>
</html>
```